Post Disaster Temporary Housing Literature Review poster

Wanting a poster design for two Emergency Management conferences we have coming up. The information to be included in the poster is capturing the purpose, findings and recommendations from a post disaster temporary housing literature review looking at “What should government consider in order to improve planning and decision making for accommodation needs after a disaster, and to support people’s transition to stable housing?”
I’d like to enhance the visual appeal through including relevant images or graphic. I am also open to reducing the text if needed.
The government group I work with focuses on the social and human side of disaster recovery so keen for any images to reflect the human aspect and not focus solely on disasters or housing.
Government and NGO's

```html
<!DOCTYPE html>
<html lang="en">
<head>
<meta charset="utf-8">
<title>Post Disaster Temporary Housing Literature Review</title>
<link href="https://fonts.googleapis.com/css2?family=Montserrat:wght@500;700;800;900&family=Open+Sans:ital,wght@0,400;0,600;0,700;1,600&display=swap" rel="stylesheet">
<style>
:root{
  --navy:#1e2140;
  --navy-2:#2b2f55;
  --magenta:#c2187a;
  --magenta-dark:#9c1163;
  --pink-soft:#fbe4ef;
  --pink-mid:#f3c3da;
  --ink:#26283d;
  --muted:#55576b;
  --white:#ffffff;
}
*{box-sizing:border-box;margin:0;padding:0}
html,body{width:1200px;height:2320px;overflow:hidden;background:var(--navy)}
body{font-family:"Open Sans",Arial,sans-serif;color:var(--ink);position:relative}
.poster{position:absolute;inset:0;background:var(--navy)}

.masthead{position:absolute;left:0;top:0;width:1200px;height:250px;background:linear-gradient(90deg,var(--magenta-dark),var(--magenta) 60%,#d2338e)}
.masthead .title{position:absolute;left:60px;top:52px;color:var(--white);font-family:"Montserrat",sans-serif;text-transform:uppercase}
.title .kicker{font-weight:700;font-size:34px;letter-spacing:2px}
.title .main{font-weight:900;font-size:54px;line-height:1.02;letter-spacing:.5px}
.masthead .art{position:absolute;right:50px;top:24px;width:310px;height:200px;border-radius:10px;background:linear-gradient(160deg,#f6e6ef,#d9a9c6)}

.summary-bar{position:absolute;left:0;top:250px;width:1200px;height:66px;background:var(--white);display:flex;align-items:center;padding:0 60px;gap:28px}
.summary-bar h2{font-family:"Montserrat",sans-serif;font-weight:900;font-size:26px;line-height:1;color:var(--navy);width:140px}
.summary-bar p{font-size:15px;color:var(--magenta);font-weight:600}

.col-left{position:absolute;left:40px;top:336px;width:600px;height:1740px;background:var(--white);padding:26px 30px}
.col-right{position:absolute;left:660px;top:336px;width:500px;height:1740px;background:var(--pink-soft);padding:26px 28px}

.sec-head{display:flex;align-items:center;gap:14px;margin-bottom:14px}
.sec-head .dot{width:44px;height:44px;border-radius:50%;background:var(--magenta);flex:none;display:flex;align-items:center;justify-content:center}
.sec-head h3{font-family:"Montserrat",sans-serif;font-weight:800;font-size:30px;color:var(--navy);text-transform:uppercase;letter-spacing:.5px}

p.body{font-size:14.5px;line-height:1.5;color:var(--muted);margin-bottom:12px}
.question-label{font-family:"Montserrat",sans-serif;font-weight:800;font-size:14px;color:var(--magenta);text-transform:uppercase;margin-bottom:4px}
.question{font-style:italic;font-weight:600;font-size:15px;line-height:1.45;color:var(--navy);margin-bottom:12px}

.sub-bar{background:var(--navy);color:var(--white);font-weight:700;font-size:14px;padding:7px 12px;margin:14px 0 10px}
.callout{background:var(--pink-soft);border-left:5px solid var(--magenta);padding:12px 14px;margin-bottom:10px}
.callout ul{padding-left:18px}
.callout li{font-size:14px;line-height:1.45;color:var(--ink);margin-bottom:6px}

.next-steps{margin-top:22px;padding-top:18px;border-top:3px solid var(--pink-mid)}

.rec{display:flex;gap:14px;margin-bottom:17px}
.rec .icon{width:46px;height:46px;border-radius:50%;background:var(--white);border:3px solid var(--magenta);flex:none;display:flex;align-items:center;justify-content:center}
.rec h4{font-family:"Montserrat",sans-serif;font-weight:800;font-size:17px;color:var(--navy);text-transform:uppercase;margin-bottom:3px}
.rec p{font-size:13px;line-height:1.42;color:var(--muted)}
.rec ul{padding-left:16px}
.rec li{font-size:13px;line-height:1.4;color:var(--muted);margin-bottom:3px}

.footer{position:absolute;left:0;top:2096px;width:1200px;height:224px;background:var(--navy)}
.brand{position:absolute;left:60px;top:62px;display:flex;align-items:center;gap:20px}
.brand .mark{width:84px;height:84px;border-radius:50%;background:var(--magenta)}
.brand .name{font-family:"Montserrat",sans-serif;font-weight:700;font-size:26px;line-height:1.2;color:var(--white)}
.contact{position:absolute;right:40px;top:30px;width:540px}
.contact .band{background:var(--magenta);color:var(--white);font-family:"Montserrat",sans-serif;font-weight:800;font-size:20px;text-transform:uppercase;padding:12px 22px;letter-spacing:.5px}
.contact .card{background:var(--white);padding:14px 22px}
.contact .person{font-family:"Montserrat",sans-serif;font-weight:900;font-size:28px;color:var(--navy);text-transform:uppercase}
.contact .role{font-size:14px;color:var(--muted);line-height:1.4}
.contact .email{font-size:14px;color:var(--magenta);font-weight:600;display:flex;align-items:center;gap:8px;margin-top:4px}
</style>
</head>
<body>
<div class="poster">

  <header class="masthead">
    <div class="title">
      <div class="kicker">Post Disaster</div>
      <div class="main">Temporary Housing<br>Literature Review</div>
    </div>
    <div class="art" role="img" aria-label="Illustration of a small row of houses with a family together in front"></div>
  </header>

  <div class="summary-bar">
    <h2>SUMMARY REPORT</h2>
    <p>The full report is available at https://library.recoverynetwork.org.au/resources/temporary-housing-review &nbsp;January 2024</p>
  </div>

  <section class="col-left">
    <div class="sec-head">
      <span class="dot"><svg width="22" height="22" viewBox="0 0 24 24"><circle cx="12" cy="12" r="9" fill="none" stroke="#fff" stroke-width="2.5"/><circle cx="12" cy="12" r="3.5" fill="#fff"/></svg></span>
      <h3>Purpose</h3>
    </div>
    <p class="body">There are currently significant challenges in supporting displaced people with timely and equitable access to emergency and temporary accommodation and possible transition to a safe, stable home in the aftermath of a disaster. This report seeks to support agencies and decision makers to formulate and implement appropriate responses for post disaster housing recovery that centre on the needs of affected communities.</p>
    <p class="question-label">The central research question underpinning this report is:</p>
    <p class="question">What should government consider in order to improve planning and decision making for accommodation needs after a disaster, and to support people's transition to stable housing?</p>
    <p class="body">The review was commissioned by the Community Recovery Network with input from an academic research partner. The findings and recommendations may be utilised by stakeholders across government and the community sector.</p>

    <div class="sec-head" style="margin-top:18px">
      <span class="dot"><svg width="22" height="22" viewBox="0 0 24 24"><circle cx="10" cy="10" r="6.5" fill="none" stroke="#fff" stroke-width="2.5"/><line x1="15" y1="15" x2="21" y2="21" stroke="#fff" stroke-width="3" stroke-linecap="round"/></svg></span>
      <h3>Findings</h3>
    </div>

    <div class="sub-bar">Leading practice in disaster housing recovery</div>
    <p class="body">The analysis of leading practice in housing recovery led to the development of a framework of criteria that could be used to identify appropriate actions by housing recovery officers and decision makers. Criteria relate to the planning and implementation of accommodation and temporary housing. The intended application is to help agencies compare options for achieving eight categories of leading practice: community engagement and empowerment; equity; safety, health, comfort and privacy; cultural and special needs; community connection; and social and technical support.</p>

    <div class="sub-bar">Innovative approaches in temporary housing</div>
    <p class="body">Innovative approaches to effective temporary housing practice are based upon the concept of resilient housing recovery, which has at least five dimensions: wellbeing, liveability, sustainability, community connection, and stability. This change of focus has two key implications:</p>
    <div class="callout">
      <ul>
        <li>The planning of post disaster housing and infrastructure programs needs to be part of the priority strategies of pre-disaster preparedness; and</li>
        <li>Strategies are needed to embed temporary housing as the first step in the design and construction of resilient housing that reconnects people with their communities and supports a permanent return home.</li>
      </ul>
    </div>
    <p class="body">These implications are explored through strategies and tools for pre-disaster planning and the development of a two-phase model for constructing stable housing through a temporary-to-permanent construction strategy.</p>

    <div class="sub-bar">A decision-making framework for resilient housing recovery</div>
    <p class="body">The framework seeks to integrate the steps in project management and to use the housing process as a tool for social recovery. The model aligns decisions at strategic and operational levels and manages the inside and outside issues of location, tenure, housing types and procurement. It has been organised into five decision categories: strategic planning, community consultation, program delivery, design and construction, and monitoring and evaluation.</p>

    <div class="next-steps">
      <div class="sec-head">
        <span class="dot"><svg width="22" height="22" viewBox="0 0 24 24"><path d="M5 12h13M13 6l6 6-6 6" fill="none" stroke="#fff" stroke-width="2.8" stroke-linecap="round" stroke-linejoin="round"/></svg></span>
        <h3>Next Steps</h3>
      </div>
      <p class="body">The Community Recovery Network is partnering with national research bodies to analyse previous post disaster temporary housing evidence and capture lived experience across Australia. The project aims to provide national guidance on the design and implementation of temporary housing from the research and lived experience.</p>
    </div>
  </section>

  <section class="col-right">
    <div class="sec-head">
      <span class="dot"><svg width="22" height="22" viewBox="0 0 24 24"><path d="M5 12.5l4.5 4.5L19 7.5" fill="none" stroke="#fff" stroke-width="3" stroke-linecap="round" stroke-linejoin="round"/></svg></span>
      <h3>Recommendations</h3>
    </div>

    <div class="rec"><span class="icon"><svg width="20" height="20" viewBox="0 0 24 24"><path d="M5 4h11l3 3v13H5z" fill="none" stroke="#c2187a" stroke-width="2.4"/></svg></span>
      <div><h4>Terminology</h4><p>Develop a standard set of terminology to describe the phases and types of accommodation displaced people may access to ensure shared understanding across governments, communities and supporting agencies.</p></div></div>

    <div class="rec"><span class="icon"><svg width="20" height="20" viewBox="0 0 24 24"><path d="M5 12.5l4.5 4.5L19 7.5" fill="none" stroke="#c2187a" stroke-width="3"/></svg></span>
      <div><h4>Principles</h4><p>Adopt common principles of leading practice in post disaster housing recovery including community connection, wellbeing, liveability, safety and sustainability, and empower people to shape support options.</p></div></div>

    <div class="rec"><span class="icon"><svg width="20" height="20" viewBox="0 0 24 24"><circle cx="12" cy="12" r="8" fill="none" stroke="#c2187a" stroke-width="2.4"/></svg></span>
      <div><h4>National Principles</h4><p>The Commonwealth and State and Territory governments should embed the agreed principles of disaster recovery in national models of resilient recovery.</p></div></div>

    <div class="rec"><span class="icon"><svg width="20" height="20" viewBox="0 0 24 24"><path d="M6 4h12v16H6zM9 9h6M9 13h6" fill="none" stroke="#c2187a" stroke-width="2.2"/></svg></span>
      <div><h4>Guidelines</h4><p>Develop resources and guidelines to support planning and operational aspects of post disaster housing.</p></div></div>

    <div class="rec"><span class="icon"><svg width="20" height="20" viewBox="0 0 24 24"><path d="M4 19l5-6 4 3 7-9" fill="none" stroke="#c2187a" stroke-width="2.6"/></svg></span>
      <div><h4>Capacity Building</h4><p>Develop capacity building resources and programs for State and Territory agencies and local governments to support pre-planning for temporary housing solutions.</p></div></div>

    <div class="rec"><span class="icon"><svg width="20" height="20" viewBox="0 0 24 24"><circle cx="12" cy="12" r="8" fill="none" stroke="#c2187a" stroke-width="2.4"/><path d="M12 7v10M9 10h5a2 2 0 010 4h-4" fill="none" stroke="#c2187a" stroke-width="2"/></svg></span>
      <div><h4>Funding</h4><p>Recognise different cost implications of temporary housing programs including long term use, and use funding streams to address the priority needs.</p></div></div>

    <div class="rec"><span class="icon"><svg width="20" height="20" viewBox="0 0 24 24"><circle cx="10" cy="10" r="6" fill="none" stroke="#c2187a" stroke-width="2.4"/><line x1="15" y1="15" x2="20" y2="20" stroke="#c2187a" stroke-width="2.8"/></svg></span>
      <div><h4>Further Research</h4><p>Undertake research into post disaster temporary housing topics such as:</p>
        <ul><li>Improving housing resilience through land-use planning and building codes.</li><li>Learnings from past programs and whether their approaches suit different communities.</li><li>Utilisation of innovative construction technologies, materials and methods.</li><li>Lived experience of people moving from temporary to permanent housing.</li></ul></div></div>

    <div class="rec"><span class="icon"><svg width="20" height="20" viewBox="0 0 24 24"><path d="M4 20V10l8-6 8 6v10z" fill="none" stroke="#c2187a" stroke-width="2.4"/></svg></span>
      <div><h4>Pilot Project</h4><p>Resource, trial and evaluate a pilot program to identify land in advance of a disaster and plan for temporary housing that supports recovery and a smooth transition to permanent homes.</p></div></div>

    <div class="rec"><span class="icon"><svg width="20" height="20" viewBox="0 0 24 24"><rect x="3" y="4" width="7" height="6" fill="none" stroke="#c2187a" stroke-width="2"/><rect x="14" y="14" width="7" height="6" fill="none" stroke="#c2187a" stroke-width="2"/><path d="M6.5 10v7h7" fill="none" stroke="#c2187a" stroke-width="2"/></svg></span>
      <div><h4>Decision Making Framework</h4><p>Adopt the outline of a decision making framework for resilient housing recovery as a national resource to guide government and community organisations in planning and implementing temporary housing.</p></div></div>

    <div class="rec"><span class="icon"><svg width="20" height="20" viewBox="0 0 24 24"><path d="M5 5h14v10H9l-4 4z" fill="none" stroke="#c2187a" stroke-width="2.3"/></svg></span>
      <div><h4>Capturing Learnings</h4><p>Establish a national repository of evaluation reports and support processes to regularly collect case studies and lessons from recovery.</p></div></div>
  </section>

  <footer class="footer">
    <div class="brand">
      <span class="mark"></span>
      <span class="name">Community Recovery<br>Network Australia</span>
    </div>
    <div class="contact">
      <div class="band">For further information contact</div>
      <div class="card">
        <div class="person">Morgan Ellery</div>
        <div class="role">National Consultant Disaster Recovery<br>Community Recovery Network</div>
        <div class="email"><svg width="18" height="14" viewBox="0 0 18 14"><rect x="1" y="1" width="16" height="12" fill="none" stroke="#c2187a" stroke-width="1.8"/><path d="M1 1l8 6 8-6" fill="none" stroke="#c2187a" stroke-width="1.8"/></svg>morgan.ellery@recoverynetwork.org.au</div>
      </div>
    </div>
  </footer>

</div>
</body>
</html>
```